Professional Website for Leading Global Private Equity Real Estate Company

The company is a leading global Private Equity Real Estate (PERE). We need a homepage design, an inner page design, and color/font tweaks to the logo (color should be more soothing than current blue used in the logo). The logo website should project the company as global, professional, experienced, trustworthy, accessible, YOUNG, DYNAMIC, hi-tech. PLEASE SEE the attached Design Brief Word Doc for details.

Target Market(s)

institional investors and wealthy private individuals

Industry/Entity Type

Finance

Number of Pages Required

2 page

Font styles to use
Sans Serif
Other font styles liked:
• either like in https://www.ferndalequay.com/ or like in presentations (Montserrat Black & Montserrat Light, Century Gothic, Blair ITC, Almoni Neue DL 4.0 AAA Medium, Almoni DL AAA)

Requirements
Must have
• new color palette that is NOT based on current logo. they want a more soothing color palette than the blue in that logo. the new color palette should project: global, professional, experienced, trustworthy, accessible, YOUNG, DYNAMIC, hi-tech.
Nice to have
• the likes these sites: https://www.ferndalequay.com/ and https://www.tvr.law/

```html
<!DOCTYPE html>
<html lang="en">
<head>
<meta charset="utf-8">
<title>Veltra Real Estate — Homepage Concepts</title>
<link href="https://fonts.googleapis.com/css2?family=Michroma&family=Montserrat:wght@400;500;600&display=swap" rel="stylesheet">
<style>
:root{
  --board:#e7e7ea;
  --ink:#2b2b2f;
  --muted:#6d6d73;
  --white:#ffffff;
  --teal:#3f8f93;
  --teal-deep:#3a7c85;
  --navy:#35477a;
  --slate:#6f6f72;
  --sand:#d2b48c;
  --wine:#a01c3a;
  --wine-deep:#8c1631;
  --terracotta:#c27560;
  --steel:#35566a;
  --paper:#f3f4f8;
  --display:"Michroma",sans-serif;
  --body:"Montserrat",sans-serif;
}
*{box-sizing:border-box;margin:0;padding:0}
html,body{width:1110px;height:1200px;overflow:hidden;background:var(--board);font-family:var(--body);color:var(--ink)}
.board{position:relative;width:1110px;height:1200px}
.concept{position:absolute;top:15px;overflow:hidden;background:var(--white)}
.abs{position:absolute}
.photo{position:absolute}
.h-display{font-family:var(--display);letter-spacing:.04em;text-transform:uppercase;line-height:1.15}
.eyebrow{font-family:var(--display);text-transform:uppercase;letter-spacing:.1em}
.body-copy{line-height:1.55;color:var(--muted)}
.rule{position:absolute;height:1px;background:currentColor}
.btn{position:absolute;display:flex;align-items:center;justify-content:center;font-family:var(--display);text-transform:uppercase;letter-spacing:.08em;white-space:nowrap}
.field{position:absolute;background:var(--white);display:flex;align-items:center;padding-left:3px;color:#999}
.nav{position:absolute;display:flex;font-family:var(--body);text-transform:uppercase;color:var(--white);white-space:nowrap}
.brand{position:absolute;display:flex;align-items:center;gap:3px;color:var(--white);font-family:var(--display);text-transform:uppercase;line-height:1.1}
.brand i{display:block;border-radius:50%;background:var(--white)}
.play{position:absolute;border-radius:50%;border:1px solid var(--white)}
.play::after{content:"";position:absolute;left:38%;top:28%;border-left:5px solid var(--white);border-top:3px solid transparent;border-bottom:3px solid transparent}
.tile-title{font-family:var(--display);text-transform:uppercase;color:var(--white);letter-spacing:.02em;line-height:1.25}
.strip-caption{position:absolute;width:60px;font-family:var(--display);text-transform:uppercase;color:var(--white);font-size:2.9px;letter-spacing:.01em;line-height:1.3}
.foot-col{position:absolute;font-family:var(--body);color:var(--ink);line-height:1.9}
.foot-col b{display:block;font-weight:500;text-transform:uppercase;letter-spacing:.03em}
.dot{display:inline-block;border-radius:50%}
</style>
</head>
<body>
<div class="board">

<!-- ===== Concept A ===== -->
<section class="concept concept-a" style="left:49px;width:246px;height:1142px">
  <div class="photo" role="img" aria-label="Business team meeting around a conference table" style="left:0;top:0;width:246px;height:145px;background:linear-gradient(105deg,#2b2e35 0%,#4e4a44 22%,#23262c 42%,#6a645c 58%,#2a2d33 74%,#5b4436 88%,#23252a 100%)"></div>
  <div class="brand" style="left:20px;top:4px;font-size:3.6px"><i style="width:8px;height:8px"></i><span>Veltra<br>Real Estate</span></div>
  <div class="nav" style="left:73px;top:10px;font-size:2.4px;gap:7px"><span>About us ▾</span><span>Our businesses ▾</span><span>Investors lobby</span><span>News</span><span>Contact us</span></div>
  <div class="btn" style="left:206px;top:8px;width:22px;height:6px;background:var(--teal);color:#fff;font-size:2.2px">Log in</div>
  <div class="play" style="left:118px;top:50px;width:9px;height:9px"></div>
  <div class="h-display abs" style="left:0;width:246px;top:64px;text-align:center;color:#fff;font-size:7px">Leading global private<br>equity real estate</div>
  <div class="btn" style="left:107px;top:83px;width:38px;height:8px;border:1px solid #fff;color:#fff;font-size:3px">About us</div>

  <div class="abs" style="left:0;top:145px;width:246px;height:103px;background:var(--paper)"></div>
  <div class="abs" role="img" aria-label="Teal circular emblem with building reflection" style="left:24px;top:160px;width:74px;height:74px;border-radius:50%;background:radial-gradient(circle at 35% 30%,#7cbcbd,#3f8f93 55%,#2b6f74)"></div>
  <div class="h-display abs" style="left:113px;top:171px;font-size:5px">Veltra Real Estate</div>
  <div class="rule" style="left:113px;top:179px;width:10px;color:var(--sand)"></div>
  <p class="body-copy abs" style="left:113px;top:184px;width:112px;font-size:2.4px">Lorem ipsum dolor sit amet, consectetur adipiscing elit, sed do eiusmod tempor incididunt ut labore et dolore enim ad minim veniam, quis nostrud exercitation ullamco laboris nisi ut aliquip ex ea</p>
  <div class="abs" style="left:113px;top:209px;display:flex;gap:14px;font-family:var(--display);font-size:6px"><span>$250<small style="display:block;font-family:var(--body);font-size:2px;color:var(--muted)">REAL ESTATE PROJECTS</small></span><span>$25B<small style="display:block;font-family:var(--body);font-size:2px;color:var(--muted)">PRIVATE EQUITY</small></span><span>$13B<small style="display:block;font-family:var(--body);font-size:2px;color:var(--muted)">FUND SOLUTIONS</small></span></div>

  <div class="h-display abs" style="left:0;width:246px;top:259px;text-align:center;font-size:5px">Our investment platforms</div>
  <div class="rule" style="left:118px;top:270px;width:10px;color:var(--ink)"></div>

  <!-- platform grid -->
  <div class="abs" style="left:21px;top:279px;width:203px;height:373px">
    <div class="abs" style="left:0;top:0;width:102px;height:75px;background:var(--slate)"></div>
    <div class="photo" role="img" aria-label="Glass office towers against blue sky" style="left:102px;top:0;width:101px;height:75px;background:linear-gradient(150deg,#c9dbee 0%,#8fb0d6 35%,#2f4f7e 65%,#5c7da8 100%)"></div>
    <div class="photo" role="img" aria-label="Hand touching private equity data screen" style="left:0;top:75px;width:102px;height:75px;background:linear-gradient(135deg,#1a2440 0%,#3c5488 40%,#8ea4d2 62%,#e6dccd 100%)"></div>
    <div class="abs" style="left:102px;top:75px;width:101px;height:75px;background:#fff"></div>
    <div class="abs" style="left:0;top:150px;width:102px;height:75px;background:var(--navy)"></div>
    <div class="photo" role="img" aria-label="Dark glass skyscrapers looking up" style="left:102px;top:150px;width:101px;height:75px;background:linear-gradient(155deg,#a9b4c3 0%,#4a5566 35%,#1b2029 70%,#39424f 100%)"></div>
    <div class="photo" role="img" aria-label="Office facade lit in pink and blue at night" style="left:0;top:225px;width:102px;height:75px;background:linear-gradient(120deg,#171b30 0%,#7a2c62 35%,#1f2442 55%,#3c6a9c 80%,#16192c 100%)"></div>
    <div class="abs" style="left:102px;top:225px;width:101px;height:75px;background:#ededee"></div>
    <div class="abs" style="left:0;top:300px;width:102px;height:73px;background:var(--teal)"></div>
    <div class="photo" role="img" aria-label="Glass tower reflecting clouds" style="left:102px;top:300px;width:101px;height:73px;background:linear-gradient(160deg,#e9f0f7 0%,#b7cbe2 40%,#5f82ad 75%,#3d5f8c 100%)"></div>
  </div>
  <div class="tile-title abs" style="left:21px;width:102px;top:289px;text-align:center;font-size:3.2px">Lorem ipsum dolor sit</div>
  <p class="abs" style="left:33px;width:78px;top:296px;text-align:center;font-size:2px;line-height:1.6;color:#eee">Sed ut perspiciatis unde omnis iste natus error sit voluptatem accusantium doloremque laudantium totam rem aperiam eaque ipsa quae ab illo inventore</p>
  <div class="btn" style="left:55px;top:345px;width:33px;height:7px;border:.5px solid #fff;color:#fff;font-size:1.8px">Learn more</div>
  <div class="tile-title abs" style="left:123px;width:101px;top:384px;text-align:center;font-size:3.2px;color:var(--ink)">Lorem ipsum dolor sit</div>
  <p class="abs body-copy" style="left:135px;width:77px;top:391px;text-align:center;font-size:2px">Sed ut perspiciatis unde omnis iste natus error sit voluptatem accusantium doloremque laudantium totam rem aperiam eaque ipsa quae ab illo inventore</p>
  <div class="btn" style="left:157px;top:421px;width:33px;height:7px;border:.5px solid var(--navy);color:var(--navy);font-size:1.8px">Learn more</div>
  <div class="tile-title abs" style="left:21px;width:102px;top:459px;text-align:center;font-size:3.2px">Lorem ipsum dolor sit</div>
  <p class="abs" style="left:33px;width:78px;top:466px;text-align:center;font-size:2px;line-height:1.6;color:#dde">Sed ut perspiciatis unde omnis iste natus error sit voluptatem accusantium doloremque laudantium totam rem aperiam eaque ipsa quae ab illo inventore</p>
  <div class="btn" style="left:57px;top:495px;width:33px;height:7px;border:.5px solid #fff;color:#fff;font-size:1.8px">Learn more</div>
  <div class="tile-title abs" style="left:123px;width:101px;top:533px;text-align:center;font-size:3.2px;color:var(--ink)">Lorem ipsum dolor sit</div>
  <p class="abs body-copy" style="left:135px;width:77px;top:540px;text-align:center;font-size:2px">Sed ut perspiciatis unde omnis iste natus error sit voluptatem accusantium doloremque laudantium totam rem aperiam eaque ipsa quae ab illo inventore</p>
  <div class="btn" style="left:157px;top:569px;width:33px;height:7px;border:.5px solid var(--navy);color:var(--navy);font-size:1.8px">Learn more</div>
  <div class="tile-title abs" style="left:21px;width:102px;top:609px;text-align:center;font-size:3.2px">Lorem ipsum dolor sit</div>
  <p class="abs" style="left:33px;width:78px;top:616px;text-align:center;font-size:2px;line-height:1.6;color:#e6f1f1">Sed ut perspiciatis unde omnis iste natus error sit voluptatem accusantium doloremque laudantium totam rem aperiam eaque ipsa quae ab illo inventore</p>
  <div class="btn" style="left:56px;top:643px;width:33px;height:7px;border:.5px solid #fff;color:#fff;font-size:1.8px">Learn more</div>

  <!-- our edge -->
  <div class="photo" role="img" aria-label="Aerial view of a city skyline" style="left:0;top:672px;width:121px;height:106px;background:linear-gradient(175deg,#e3e8ee 0%,#b9c2cc 25%,#8e97a1 45%,#c4b8a6 62%,#5d646d 80%,#3e444c 100%)"></div>
  <div class="abs" style="left:121px;top:672px;width:125px;height:106px;background:#f1f1f2"></div>
  <div class="h-display abs" style="left:136px;top:704px;font-size:5px">Our edge</div>
  <div class="rule" style="left:136px;top:712px;width:10px;color:var(--ink)"></div>
  <p class="body-copy abs" style="left:136px;top:717px;width:95px;font-size:2.2px">Lorem ipsum dolor sit amet, consectetur adipiscing elit, sed do eiusmod tempor incididunt ut co laboris nisi ut aliquip ex ea commodo consequat. Duis aute irure dolor in reprehende. Aabor et dolore magna aliqua. Ut enim ad minim veniam, quis nostrud exercitation ullamco laboris nisi ut aliquip ex ea commodo.</p>
  <div class="btn" style="left:136px;top:760px;width:56px;height:10px;background:var(--navy);color:#fff;font-size:2.2px">Investor information</div>

  <!-- stay updated -->
  <div class="photo" role="img" aria-label="Gray city skyline backdrop" style="left:0;top:778px;width:246px;height:78px;background:linear-gradient(180deg,#9a9a9c 0%,#858587 45%,#6a6a6c 70%,#767678 100%)"></div>
  <div class="h-display abs" style="left:0;width:246px;top:802px;text-align:center;color:#fff;font-size:5.5px">Stay updated</div>
  <div class="abs" style="left:0;width:246px;top:812px;text-align:center;color:#eee;font-size:2.5px">Get our latest insights, firm announcements and Charitable Foundation updates.</div>
  <div class="field" style="left:37px;top:821px;width:62px;height:10px;font-size:2.2px">NAME*</div>
  <div class="field" style="left:101px;top:821px;width:62px;height:10px;font-size:2.2px">EMAIL*</div>
  <div class="btn" style="left:165px;top:821px;width:41px;height:10px;background:var(--sand);color:#fff;font-size:2.4px">Subscribe</div>

  <!-- responsibility -->
  <div class="h-display abs" style="left:25px;top:882px;font-size:5px">Our responsibility</div>
  <div class="rule" style="left:25px;top:890px;width:10px;color:var(--ink)"></div>
  <p class="body-copy abs" style="left:25px;top:894px;width:88px;font-size:2.2px">Lorem ipsum dolor sit amet, consectetur adipiscing elit, sed do eiusmod tempor incididunt ut. Aabor et dolore magna aliqua. Ut enim ad minim veniam, quis nostrud exercitation ullamco laboris nisi ut aliquip ex ea commodo consequat. Duis aute irure dolor in reprehenderit.</p>
  <div class="btn" style="left:25px;top:938px;width:35px;height:8px;border:.5px solid var(--navy);color:var(--navy);font-size:2px">Learn more</div>
  <div class="photo" role="img" aria-label="Colleagues discussing around a laptop" style="left:121px;top:856px;width:125px;height:102px;background:linear-gradient(120deg,#3a3230 0%,#b08a55 25%,#e2cfa8 45%,#5c4a3c 65%,#c9a66b 85%,#2e2a28 100%)"></div>

  <!-- get in touch -->
  <div class="photo" role="img" aria-label="Faded city skyline backdrop" style="left:0;top:958px;width:246px;height:106px;background:linear-gradient(180deg,#f3f3f4 0%,#e4e5e8 50%,#d3d5d9 100%)"></div>
  <div class="h-display abs" style="left:0;width:246px;top:978px;text-align:center;font-size:5.5px">Get in touch</div>
  <div class="field" style="left:57px;top:991px;width:65px;height:8px;font-size:2px">First Name</div>
  <div class="field" style="left:124px;top:991px;width:65px;height:8px;font-size:2px">Last Name</div>
  <div class="field" style="left:57px;top:1001px;width:65px;height:8px;font-size:2px">Phone Number</div>
  <div class="field" style="left:124px;top:1001px;width:65px;height:8px;font-size:2px">Email address</div>
  <div class="field" style="left:57px;top:1011px;width:132px;height:16px;align-items:flex-start;padding-top:2px;font-size:2px">Message</div>
  <div class="btn" style="left:104px;top:1035px;width:42px;height:9px;background:var(--teal);color:#fff;font-size:2px">Submit message</div>

  <!-- footer -->
  <div class="abs" style="left:0;top:1064px;width:246px;height:78px;background:var(--navy)"></div>
  <div class="foot-col" style="left:30px;top:1072px;font-size:2.2px;color:#dfe3ef"><b>Important links</b>About Us<br>Our Businesses<br>Investor Lobby<br>News<br>Contact Us</div>
  <div class="foot-col" style="left:76px;top:1072px;font-size:2.2px;color:#dfe3ef"><b>Explore Veltra Real Estate</b>Private Equity<br>Real Estate<br>Credit<br>Strategic Partners<br>Tactical Opportunities<br>Infrastructure</div>
  <div class="foot-col" style="left:123px;top:1080px;font-size:2.2px;color:#dfe3ef">Insurance Solutions<br>Life Sciences<br>Portfolio Operations<br>Technology and Innovations<br>Registered Products</div>
  <div class="foot-col" style="left:171px;top:1072px;font-size:2.2px;color:#dfe3ef"><b>Contact details</b>420 N Harbor Way Suite B<br>Cedar Point, FL 30211<br>555-210-4478<br>hello@veltrarealestate.com</div>
  <div class="abs" style="left:173px;top:1113px;display:flex;gap:2px"><i class="dot" style="width:4px;height:4px;background:#fff"></i><i class="dot" style="width:4px;height:4px;background:#fff"></i><i class="dot" style="width:4px;height:4px;background:#fff"></i><i class="dot" style="width:4px;height:4px;background:#fff"></i></div>
  <div class="abs" style="left:22px;top:1132px;font-size:1.8px;color:#7d8ab0">Copyright © 2022 Veltra Realestate</div>
  <div class="abs" style="left:170px;top:1132px;font-size:1.8px;color:#7d8ab0">Terms of Use | Sitemap | Privacy Policy</div>
</section>

<!-- ===== Concept B ===== -->
<section class="concept concept-b" style="left:332px;width:342px;height:1135px">
  <div class="photo" role="img" aria-label="High-rise towers over a city at dusk" style="left:0;top:0;width:342px;height:201px;background:linear-gradient(180deg,#24242b 0%,#3c3440 18%,#6a5a52 36%,#8b7a66 48%,#4a4a4e 62%,#2e2f33 80%,#4b4b4e 100%)"></div>
  <div class="brand" style="left:29px;top:4px;font-size:4.5px"><i style="width:14px;height:14px"></i><span>Veltra<br>Real Estate</span></div>
  <div class="nav" style="left:101px;top:10px;font-size:3.7px;gap:10px"><span>About us ▾</span><span>Our businesses ▾</span><span>Investors lobby</span><span>News</span><span>Contact us</span></div>
  <div class="btn" style="left:285px;top:7px;width:33px;height:10px;border:1px solid #fff;border-radius:6px;color:#fff;font-family:var(--body);font-size:3.5px">Log in</div>
  <div class="play" style="left:166px;top:73px;width:14px;height:14px"></div>
  <div class="h-display abs" style="left:0;width:342px;top:94px;text-align:center;color:#fff;font-size:10px;line-height:1.15">Leading global private<br>equity real estate</div>
  <div class="btn" style="left:146px;top:120px;width:54px;height:13px;border:1px solid #fff;color:#fff;font-size:4.5px">About us</div>

  <div class="abs" style="left:0;top:201px;width:342px;height:139px;background:#f2f2f2"></div>
  <div class="eyebrow abs" style="left:39px;top:227px;color:var(--wine);font-size:3.5px">Who we are</div>
  <div class="h-display abs" style="left:39px;top:234px;font-size:9px">About Veltra<br>Real Estate</div>
  <div class="rule" style="left:39px;top:262px;width:12px;color:var(--ink)"></div>
  <p class="body-copy abs" style="left:39px;top:266px;width:130px;font-size:4.2px">Lorem ipsum dolor sit amet, consectetur adipiscing elit, sed do eiusmod tempor incididunt ut labore et dolore<br><br>Ut enim ad minim veniam, quis nostrud exercitation ullamco laboris nisi ut aliquip ex ea commodo consequat. Duis aute irure dolor in reprehenderi</p>
  <div class="abs" style="left:215px;top:224px;width:72px;font-family:var(--display);color:var(--wine);font-size:9.5px">$250<div style="font-family:var(--body);font-size:3.6px;color:var(--muted);margin-top:2px">REAL ESTATE PROJECTS</div><div style="height:1px;background:#ccc;margin-top:9px"></div></div>
  <div class="abs" style="left:215px;top:256px;width:72px;font-family:var(--display);color:var(--wine);font-size:9.5px">$25B<div style="font-family:var(--body);font-size:3.6px;color:var(--muted);margin-top:2px">PRIVATE EQUITY</div><div style="height:1px;background:#ccc;margin-top:9px"></div></div>
  <div class="abs" style="left:215px;top:290px;width:72px;font-family:var(--display);color:var(--wine);font-size:9.5px">$13B<div style="font-family:var(--body);font-size:3.6px;color:var(--muted);margin-top:2px">FUND SOLUTIONS</div></div>

  <div class="eyebrow abs" style="left:0;width:342px;top:353px;text-align:center;color:var(--teal);font-size:3.5px">What we do</div>
  <div class="h-display abs" style="left:0;width:342px;top:360px;text-align:center;font-size:7.8px">Our investment platforms</div>
  <div class="rule" style="left:163px;top:372px;width:16px;color:var(--ink)"></div>

  <div class="photo" role="img" aria-label="Private equity data interface" style="left:0;top:383px;width:67px;height:81px;background:linear-gradient(135deg,#232325 0%,#5a5a5c 40%,#9a9a9c 60%,#3a3a3c 100%)"></div>
  <div class="abs" style="left:68px;top:383px;width:68px;height:81px;background:var(--wine)"></div>
  <div class="photo" role="img" aria-label="Modern glass office building" style="left:137px;top:383px;width:69px;height:81px;background:linear-gradient(170deg,#e2e2e2 0%,#b5b5b5 35%,#6a6a6c 65%,#3b3b3d 100%)"></div>
  <div class="photo" role="img" aria-label="Businessman facing city skyline" style="left:207px;top:383px;width:68px;height:81px;background:linear-gradient(170deg,#d0d0d0 0%,#9a9a9a 40%,#4e4e50 70%,#2b2b2d 100%)"></div>
  <div class="photo" role="img" aria-label="Misty city towers" style="left:276px;top:383px;width:66px;height:81px;background:linear-gradient(170deg,#dadada 0%,#aaaaab 40%,#6c6c6e 75%,#444446 100%)"></div>
  <div class="strip-caption" style="left:5px;top:449px">Sed ut perspiciatis<br>unde omnis</div>
  <div class="strip-caption" style="left:76px;top:406px">Sed ut perspiciatis<br>unde omnis</div>
  <p class="abs" style="left:76px;top:415px;width:55px;font-size:3px;line-height:1.45;color:#f0c9d1">Lorem ipsum dolor sit amet, consectetur adipiscing elit, sed do eiusmod tempor incididunt ut labore et</p>
  <div class="btn" style="left:76px;top:439px;width:36px;height:9px;border:1px solid #fff;border-radius:6px;color:#fff;font-size:2.4px">Learn more</div>
  <div class="strip-caption" style="left:142px;top:449px">Vatem quia voluptas<br>sit aspernatur</div>
  <div class="strip-caption" style="left:212px;top:449px">Sed ut perspiciatis<br>unde omnis</div>
  <div class="strip-caption" style="left:282px;top:449px">Nemo enim ipsam<br>voluptatem</div>

  <div class="abs" style="left:0;top:464px;width:342px;height:154px;background:#f7f7f7"></div>
  <div class="photo" role="img" aria-label="Twin glass skyscrapers from below" style="left:0;top:464px;width:342px;height:154px;clip-path:polygon(217px 0,342px 0,342px 154px,148px 154px);background:linear-gradient(165deg,#f4f4f4 0%,#cfcfcf 30%,#7c7c7e 50%,#2a2a2c 70%,#8c8c8e 88%,#d8d8d8 100%)"></div>
  <div class="h-display abs" style="left:33px;top:508px;font-size:8px">Our edge</div>
  <div class="rule" style="left:33px;top:520px;width:14px;color:var(--ink)"></div>
  <p class="body-copy abs" style="left:33px;top:525px;width:130px;font-size:3.7px">Lorem ipsum dolor sit amet, consectetur adipiscing elit, sed do eiusmod tempor incididunt ut co laboris nisi ut aliquip ex ea commodo consequat. Duis aute irure dolor in reprehende<br><br>Aabor et dolore magna aliqua. Ut enim ad minim veniam, quis nostrud exercitation ullamco laboris nisi ut aliquip ex ea commodo consequat. Duis aute irure dolor in reprehenderitd exercitation</p>
  <div class="btn" style="left:33px;top:574px;width:78px;height:15px;background:var(--wine);color:#fff;font-size:3.3px">Investor information</div>

  <div class="photo" role="img" aria-label="Dark city skyline backdrop" style="left:0;top:618px;width:342px;height:110px;background:linear-gradient(180deg,#3a3a3c 0%,#505052 40%,#6e6e70 65%,#58585a 100%)"></div>
  <div class="h-display abs" style="left:0;width:342px;top:649px;text-align:center;color:#fff;font-size:8.5px">Stay updated</div>
  <div class="abs" style="left:0;width:342px;top:664px;text-align:center;color:#eee;font-size:4.2px">Get our latest insights, firm announcements and Charitable Foundation updates.</div>
  <div class="field" style="left:55px;top:678px;width:87px;height:15px;font-size:3.2px;padding-left:6px">NAME*</div>
  <div class="field" style="left:145px;top:678px;width:87px;height:15px;font-size:3.2px;padding-left:6px">EMAIL*</div>
  <div class="btn" style="left:235px;top:678px;width:57px;height:15px;background:var(--wine);color:#fff;font-size:4px">Subscribe</div>

  <div class="photo" role="img" aria-label="Colleagues collaborating at a laptop" style="left:0;top:728px;width:342px;height:150px;clip-path:polygon(0 0,136px 0,205px 150px,0 150px);background:linear-gradient(120deg,#5e5e60 0%,#9c9c9e 22%,#e4e4e5 40%,#7a7a7c 55%,#cfcfd0 72%,#3e3e40 100%)"></div>
  <div class="h-display abs" style="left:197px;top:769px;font-size:7.5px">Our responsibility</div>
  <div class="rule" style="left:197px;top:781px;width:14px;color:var(--ink)"></div>
  <p class="body-copy abs" style="left:198px;top:786px;width:122px;font-size:3.6px">Lorem ipsum dolor sit amet, consectetur adipiscing elit, sed do eiusmod tempor incididunt ut<br><br>Aabor et dolore magna aliqua. Ut enim ad minim veniam, quis nostrud exercitation ullamco laboris nisi ut aliquip ex ea commodo consequat. Duis aute irure dolor in reprehenderitd exercitationa aliqua. Ut enim ad minim veniam.</p>
  <div class="btn" style="left:199px;top:829px;width:48px;height:13px;border:1px solid var(--wine);color:var(--wine);font-size:3.3px">Learn more</div>

  <div class="abs" style="left:0;top:878px;width:342px;height:147px;background:linear-gradient(120deg,#a01c3a 0%,#a41f3e 45%,#8c1631 70%,#b02a48 100%)"></div>
  <div class="eyebrow abs" style="left:34px;top:905px;color:#f3cbd4;font-size:3.6px">Contact us</div>
  <div class="h-display abs" style="left:34px;top:911px;color:#fff;font-size:9px">Get in touch</div>
  <div class="field" style="left:34px;top:928px;width:69px;height:11px;background:transparent;border:.6px solid #d98a9c;color:#f2d0d7;font-size:3px;padding-left:5px">First Name</div>
  <div class="field" style="left:104px;top:928px;width:71px;height:11px;background:transparent;border:.6px solid #d98a9c;color:#f2d0d7;font-size:3px;padding-left:5px">Last Name</div>
  <div class="field" style="left:34px;top:941px;width:69px;height:11px;background:transparent;border:.6px solid #d98a9c;color:#f2d0d7;font-size:3px;padding-left:5px">Phone Number</div>
  <div class="field" style="left:104px;top:941px;width:71px;height:11px;background:transparent;border:.6px solid #d98a9c;color:#f2d0d7;font-size:3px;padding-left:5px">Email address</div>
  <div class="field" style="left:34px;top:954px;width:141px;height:22px;background:transparent;border:.6px solid #d98a9c;color:#f2d0d7;font-size:3px;padding:3px 5px;align-items:flex-start">Message</div>
  <div class="btn" style="left:34px;top:981px;width:59px;height:13px;border:1px solid #fff;color:#fff;font-size:3.4px">Submit message</div>

  <div class="foot-col" style="left:34px;top:1041px;font-size:3.3px"><b style="font-size:3.8px;margin-bottom:2px">Important links</b>About Us<br>Our Businesses<br>Investor Lobby<br>News<br>Contact Us</div>
  <div class="foot-col" style="left:100px;top:1041px;font-size:3.3px"><b style="font-size:3.8px;margin-bottom:2px">Explore Veltra Real Estate</b>Private Equity<br>Real Estate<br>Credit<br>Strategic Partners<br>Tactical Opportunities<br>Infrastructure</div>
  <div class="foot-col" style="left:158px;top:1049px;font-size:3.3px">Insurance Solutions<br>Life Sciences<br>Portfolio Operations<br>Technology and Innovations<br>Registered Products</div>
  <div class="abs" style="left:221px;top:1040px;width:1px;height:68px;background:#ccc"></div>
  <div class="foot-col" style="left:240px;top:1041px;font-size:3.3px;line-height:1.5"><b style="font-size:3.8px;margin-bottom:6px">Contact details</b></div>
  <svg class="abs" style="left:240px;top:1052px" width="8" height="40" viewBox="0 0 8 40"><path d="M4 0a3 3 0 0 1 3 3c0 2.2-3 5-3 5S1 5.2 1 3a3 3 0 0 1 3-3z" fill="#333"/><circle cx="4" cy="3" r="1" fill="#fff"/><circle cx="4" cy="16" r="3.2" fill="#333"/><path d="M2.6 14.6l1 1.6 1.8 1.2" stroke="#fff" stroke-width=".7" fill="none"/><circle cx="4" cy="29" r="3.2" fill="#333"/><rect x="2.2" y="27.8" width="3.6" height="2.4" fill="none" stroke="#fff" stroke-width=".5"/></svg>
  <div class="abs" style="left:252px;top:1051px;font-size:3.3px;line-height:1.3">420 N Harbor Way Suite B<br>Cedar Point, FL 30211</div>
  <div class="abs" style="left:252px;top:1066px;font-size:3.6px;font-weight:600">555-210-4478</div>
  <div class="abs" style="left:252px;top:1079px;font-size:3.3px">hello@veltrarealestate.com</div>
  <div class="abs" style="left:241px;top:1089px;display:flex;gap:2px"><i class="dot" style="width:7px;height:7px;background:#555"></i><i class="dot" style="width:7px;height:7px;background:#888"></i><i class="dot" style="width:7px;height:7px;background:#888"></i><i class="dot" style="width:7px;height:7px;background:#aaa"></i></div>
  <div class="abs" style="left:0;top:1114px;width:342px;height:1px;background:#e0e0e0"></div>
  <div class="abs" style="left:32px;top:1120px;font-size:3px;color:var(--muted)">Copyright © 2022 Veltra Realestate</div>
  <div class="abs" style="left:236px;top:1120px;font-size:3px;color:var(--muted)">Terms of Use &nbsp;|&nbsp; Sitemap &nbsp;|&nbsp; Privacy Policy</div>
</section>

<!-- ===== Concept C ===== -->
<section class="concept concept-c" style="left:706px;width:311px;height:1152px">
  <div class="photo" role="img" aria-label="Mountain range at twilight" style="left:0;top:0;width:311px;height:180px;background:linear-gradient(180deg,#1f45c0 0%,#3356b8 22%,#6a6fa8 40%,#b88a8c 52%,#5a5470 62%,#2b3350 75%,#1a2236 88%,#121826 100%)"></div>
  <div class="brand" style="left:25px;top:5px;font-size:3.8px"><i style="width:12px;height:12px"></i><span>Veltra<br>Real Estate</span></div>
  <div class="nav" style="left:107px;top:10px;font-size:2.9px;gap:7px"><span>About us ▾</span><span>Our businesses ▾</span><span>Investors lobby</span><span>News</span><span>Contact us</span></div>
  <div class="btn" style="left:261px;top:7px;width:27px;height:8px;border:1px solid #fff;color:#fff;font-family:var(--body);font-size:2.8px">Log in</div>
  <div class="eyebrow abs" style="left:27px;top:63px;color:#dfe4f3;font-size:3.6px">Veltra real estate</div>
  <div class="h-display abs" style="left:26px;top:71px;color:#fff;font-size:9.5px;line-height:1.1">Leading global<br>private equity<br>real estate</div>
  <div class="btn" style="left:29px;top:107px;width:40px;height:10px;border:1px solid #fff;color:#fff;font-size:3px">About us</div>
  <div class="abs" style="left:201px;top:70px;width:22px;height:22px;border-radius:50%;background:#fff"></div>
  <svg class="abs" style="left:201px;top:70px" width="22" height="22" viewBox="0 0 22 22"><path d="M9 7l6 4-6 4z" fill="#111"/></svg>
  <div class="abs" style="left:0;width:311px;top:161px;text-align:center;color:#fff;font-size:2.8px;letter-spacing:.1em">SCROLL DOWN</div>
  <svg class="abs" style="left:152px;top:166px" width="7" height="5" viewBox="0 0 7 5"><path d="M1 1l2.5 2.5L6 1" stroke="#fff" fill="none"/></svg>

  <div class="abs" role="img" aria-label="Faint circular emblem" style="left:105px;top:192px;width:100px;height:100px;border-radius:50%;background:#f4f4f5"></div>
  <div class="eyebrow abs" style="left:0;width:311px;top:212px;text-align:center;color:var(--teal);font-size:3px">Who we are</div>
  <div class="h-display abs" style="left:0;width:311px;top:218px;text-align:center;font-size:8px">Veltra Real Estate</div>
  <div class="rule" style="left:150px;top:229px;width:10px;color:var(--ink)"></div>
  <p class="body-copy abs" style="left:46px;width:219px;top:236px;text-align:center;font-size:4px">Lorem ipsum dolor sit amet, consectetur adipiscing elit, sed do eiusmod tempor incididunt ut labore et doloreUt enim ad minim veniam, quis nostrud exercitation ullamcoea Lorem ipsum dolor sit amet, consectetur adipiscingLorem ipsum dolor sit.</p>
  <div class="abs" style="left:36px;top:278px;width:240px;display:flex;justify-content:space-between;text-align:center;font-family:var(--display);color:var(--teal);font-size:8.5px">
    <span>$250<small style="display:block;font-family:var(--body);font-size:3px;color:var(--ink)">REAL ESTATE PROJECTS</small></span>
    <span>$25B<small style="display:block;font-family:var(--body);font-size:3px;color:var(--ink)">PRIVATE EQUITY</small></span>
    <span>$13B<small style="display:block;font-family:var(--body);font-size:3px;color:var(--ink)">FUND SOLUTIONS</small></span>
    <span>$120B<small style="display:block;font-family:var(--body);font-size:3px;color:var(--ink)">CREDIT &amp; INSURANCE</small></span>
  </div>
  <div class="abs" style="left:157px;top:325px;width:1px;height:15px;background:#888"></div>

  <div class="photo" role="img" aria-label="Terracotta-tinted mountain backdrop" style="left:0;top:340px;width:311px;height:195px;background:linear-gradient(180deg,#c47862 0%,#b96b56 35%,#c88069 55%,#b4654f 80%,#c27a64 100%)"></div>
  <div class="eyebrow abs" style="left:0;width:311px;top:355px;text-align:center;color:#fbe7e1;font-size:3px">Services platform</div>
  <div class="h-display abs" style="left:0;width:311px;top:361px;text-align:center;color:#fff;font-size:8px">Our investment<br>platforms</div>
  <div class="rule" style="left:150px;top:382px;width:10px;color:#fff"></div>
  <div class="photo" role="img" aria-label="Glass tower against sky" style="left:31px;top:390px;width:82px;height:56px;background:linear-gradient(150deg,#d5e1ee 0%,#95b3d6 35%,#2e4c79 65%,#1d3154 100%)"></div>
  <div class="abs" style="left:115px;top:390px;width:82px;height:56px;background:#163a5c;outline:.6px solid #7fb3c9;outline-offset:-2px"></div>
  <div class="photo" role="img" aria-label="Dark glass skyscrapers" style="left:199px;top:390px;width:82px;height:56px;background:linear-gradient(150deg,#d3dbe6 0%,#8e9bb0 35%,#2a3445 65%,#1b2230 100%)"></div>
  <div class="photo" role="img" aria-label="Office facade lit at night" style="left:73px;top:451px;width:82px;height:56px;background:linear-gradient(120deg,#171b30 0%,#7a2c62 35%,#1f2442 55%,#3c6a9c 80%,#16192c 100%)"></div>
  <div class="photo" role="img" aria-label="Glass tower reflecting clouds" style="left:157px;top:451px;width:82px;height:56px;background:linear-gradient(160deg,#eef3f8 0%,#bccfe4 40%,#6a8cb6 75%,#3f5f8d 100%)"></div>
  <div class="tile-title abs" style="left:41px;top:438px;font-size:3px">Lorem ipsum dolor sit</div>
  <div class="tile-title abs" style="left:115px;width:82px;top:405px;text-align:center;font-size:2.9px">Sed perspiciati<br>lorem ipsum dolor sit</div>
  <p class="abs" style="left:122px;width:68px;top:415px;text-align:center;font-size:2.3px;color:#d0dde8;line-height:1.4">Lorem ipsum dolor sit amet, consectetur adipiscing elit sed do eiusmod tempor</p>
  <div class="btn" style="left:141px;top:426px;width:30px;height:7px;border:.6px solid #fff;color:#fff;font-size:2px">Learn more</div>
  <div class="tile-title abs" style="left:211px;top:438px;font-size:3px">Lorem ipsum dolor sit</div>
  <div class="tile-title abs" style="left:81px;top:499px;font-size:3px">Lorem ipsum dolor sit</div>
  <div class="tile-title abs" style="left:166px;top:499px;font-size:3px">Lorem ipsum dolor sit</div>

  <svg class="abs" style="left:32px;top:552px" width="122" height="106" viewBox="0 0 122 106" role="img" aria-label="Twin glass skyscrapers in a hexagon frame">
    <defs><linearGradient id="hexFill" x1="0" y1="0" x2="1" y2="1"><stop offset="0" stop-color="#eef1f3"/><stop offset=".35" stop-color="#a9b4bc"/><stop offset=".6" stop-color="#56636d"/><stop offset="1" stop-color="#2a333a"/></linearGradient></defs>
    <polygon points="30,1 92,1 121,53 92,105 30,105 1,53" fill="url(#hexFill)" stroke="#57b3b7" stroke-width=".8"/>
  </svg>
  <div class="h-display abs" style="left:167px;top:580px;font-size:8px">Our edge</div>
  <div class="rule" style="left:167px;top:592px;width:14px;color:var(--ink)"></div>
  <p class="body-copy abs" style="left:167px;top:596px;width:118px;font-size:3.3px">Lorem ipsum dolor sit amet, consectetur adipiscing elit, sed do eiusmod tempor incididunt ut co laboris nisi ut aliquip ex ea commodo consequat.<br><br>Aabor et dolore magna aliqua. Ut enim ad minim veniam, quis nostrud exercitation ullamco laboris &nbsp;et dolore</p>
  <div class="btn" style="left:167px;top:631px;width:68px;height:13px;background:var(--teal);color:#fff;font-size:3px">Investor information</div>

  <div class="photo" role="img" aria-label="Blue-tinted city skyline backdrop" style="left:0;top:676px;width:311px;height:100px;background:linear-gradient(180deg,#33556a 0%,#3f6173 40%,#4c6c7d 65%,#2d4a5c 100%)"></div>
  <div class="h-display abs" style="left:0;width:311px;top:702px;text-align:center;color:#fff;font-size:7.5px">Stay updated</div>
  <div class="abs" style="left:0;width:311px;top:715px;text-align:center;color:#e3ebef;font-size:3.8px">Get our latest insights, firm announcements and Charitable Foundation updates.</div>
  <div class="field" style="left:53px;top:730px;width:79px;height:13px;font-size:3px;padding-left:5px">NAME*</div>
  <div class="field" style="left:134px;top:730px;width:79px;height:13px;font-size:3px;padding-left:5px">EMAIL*</div>
  <div class="btn" style="left:215px;top:730px;width:52px;height:13px;background:#d9745a;color:#fff;font-size:3.6px">Subscribe</div>

  <div class="h-display abs" style="left:32px;top:807px;font-size:7px">Our responsibility</div>
  <div class="rule" style="left:32px;top:818px;width:14px;color:var(--ink)"></div>
  <p class="body-copy abs" style="left:32px;top:822px;width:115px;font-size:3.3px">Lorem ipsum dolor sit amet, consectetur adipiscing elit, sed do eiusmod tempor incididunt ut co laboris nisi ut aliquip ex ea commodo consequat.<br><br>Aabor et dolore magna aliqua. Ut enim ad minim veniam, quis nostrud exercitation ullamco laboris &nbsp;et dolore</p>
  <div class="btn" style="left:30px;top:871px;width:68px;height:13px;background:var(--teal);color:#fff;font-size:3px">Investor information</div>
  <div class="photo" role="img" aria-label="Colleagues collaborating at a laptop in a bright office" style="left:156px;top:776px;width:155px;height:147px;background:linear-gradient(120deg,#3d4a57 0%,#8fa6bb 22%,#e8eaec 40%,#c9b9a4 55%,#6f8294 72%,#2f3b47 100%)"></div>

  <div class="photo" role="img" aria-label="Teal-tinted mountain backdrop" style="left:0;top:923px;width:311px;height:135px;background:linear-gradient(180deg,#3a7c85 0%,#44838c 35%,#4f8d95 55%,#2f6a73 100%)"></div>
  <div class="eyebrow abs" style="left:33px;top:954px;color:#d4eaec;font-size:3px">Contact us</div>
  <div class="h-display abs" style="left:33px;top:960px;color:#fff;font-size:7.5px">Get in touch<br>with us</div>
  <div class="abs" style="left:129px;top:952px;width:67px;height:8px;border-bottom:.6px solid #cfe3e5;color:#d4eaec;font-size:3px">⚲ First Name</div>
  <div class="abs" style="left:204px;top:952px;width:67px;height:8px;border-bottom:.6px solid #cfe3e5;color:#d4eaec;font-size:3px">⚲ Last Name</div>
  <div class="abs" style="left:129px;top:966px;width:67px;height:8px;border-bottom:.6px solid #cfe3e5;color:#d4eaec;font-size:3px">☏ Phone Number</div>
  <div class="abs" style="left:204px;top:966px;width:67px;height:8px;border-bottom:.6px solid #cfe3e5;color:#d4eaec;font-size:3px">✉ Email address</div>
  <div class="abs" style="left:129px;top:983px;width:142px;height:19px;border-bottom:.6px solid #cfe3e5;color:#d4eaec;font-size:3px">Message</div>
  <div class="btn" style="left:130px;top:1013px;width:53px;height:12px;background:#d9745a;color:#fff;font-size:3px">Submit message</div>

  <div class="foot-col" style="left:34px;top:1071px;font-size:3px"><b style="color:var(--steel);font-size:3.3px;margin-bottom:2px">Important links</b><span style="color:var(--steel)">About Us<br>Our Businesses<br>Investor Lobby<br>News<br>Contact Us</span></div>
  <div class="foot-col" style="left:98px;top:1071px;font-size:3px"><b style="color:var(--steel);font-size:3.3px;margin-bottom:2px">Explore Veltra Real Estate</b><span style="color:var(--steel)">Private Equity<br>Real Estate<br>Credit<br>Strategic Partners<br>Tactical Opportunities<br>Infrastructure</span></div>
  <div class="foot-col" style="left:150px;top:1078px;font-size:3px;color:var(--steel)">Insurance Solutions<br>Life Sciences<br>Portfolio Operations<br>Technology and Innovations<br>Registered Products</div>
  <div class="abs" style="left:207px;top:1070px;width:1px;height:60px;background:#ccc"></div>
  <div class="foot-col" style="left:222px;top:1071px;font-size:3.3px"><b style="color:var(--steel)">Contact details</b></div>
  <svg class="abs" style="left:222px;top:1080px" width="8" height="40" viewBox="0 0 8 40"><path d="M4 0a3 3 0 0 1 3 3c0 2.2-3 5-3 5S1 5.2 1 3a3 3 0 0 1 3-3z" fill="#2f5b7a"/><circle cx="4" cy="3" r="1" fill="#fff"/><circle cx="4" cy="15" r="3" fill="#2f5b7a"/><path d="M2.7 13.7l1 1.5 1.6 1.1" stroke="#fff" stroke-width=".6" fill="none"/><circle cx="4" cy="25" r="3" fill="#2f5b7a"/><rect x="2.3" y="23.9" width="3.4" height="2.2" fill="none" stroke="#fff" stroke-width=".5"/></svg>
  <div class="abs" style="left:233px;top:1080px;font-size:3px;line-height:1.3;color:var(--steel)">420 N Harbor Way Suite B<br>Cedar Point, FL 30211</div>
  <div class="abs" style="left:233px;top:1092px;font-size:3.3px;font-weight:600;color:var(--steel)">555-210-4478</div>
  <div class="abs" style="left:233px;top:1101px;font-size:3px;color:var(--steel)">hello@veltrarealestate.com</div>
  <div class="abs" style="left:223px;top:1111px;display:flex;gap:2px"><i class="dot" style="width:6px;height:6px;background:#2f5b7a"></i><i class="dot" style="width:6px;height:6px;background:#6f8fa6"></i><i class="dot" style="width:6px;height:6px;background:#6f8fa6"></i><i class="dot" style="width:6px;height:6px;background:#a3b6c4"></i></div>
  <div class="abs" style="left:0;top:1134px;width:311px;height:1px;background:#e0e0e0"></div>
  <div class="abs" style="left:33px;top:1140px;font-size:2.8px;color:var(--steel)">Copyright © 2022 Veltra Realestate</div>
  <div class="abs" style="left:218px;top:1140px;font-size:2.8px;color:var(--steel)">Terms of Use &nbsp;|&nbsp; Sitemap &nbsp;|&nbsp; Privacy Policy</div>
</section>

</div>
</body>
</html>
```